Salmon Shop that sells both wholesale and retail salmon in a variety of ways.

"Reef Harvest" is a business that is selling atlantic salmon in every way possible. We will be a salmon butcher to the public for retail purchase and we will also be out and about trying to sell our products to restaurants cafes and any other wholesale way. Our product is from Tasmania but we will be trading on the Sunshine Coast. The shop design has an urban, rustic feel and very much about the product. One of the owners has worked on salmon farms for 15 years and we want it to be very specialised and quality. I have nothing to offer you to help with this design....I would like both a salmon on the card, not sure if image or silohette is best and would like the other side to have a fillet with a tag of some sort. We are looking for a logo also. Use a photo of an Atlantic Salmon, Atlantic Salmon have two fins along the back.
Updates

Project Deadline Extended Reason: I am extending the deadline as I have still not got exactly what I want. All designers have added something great to what I am after and I just need someone to pull it all together. I have put in a new brief with a sketched image to help so we can get this perfect. Please read all the instructions. Thank you Added Monday, February 16, 2015

Target Market(s)

Restaurants, cafes

Industry/Entity Type

Retail

Contact Information for Business Card

Reef Harvest (Not to have "Shop" at the end.Shop 12/130-164 Brisbane RdMooloolaba 4557

Colors
1c66ab

Requirements
Must have
• logo for reef harvest with the S being salmon fillet of fresh salmon on white platemap of tasmaniasepia /black and white image of atlantic salmon
Nice to have
• fillet of salmonmap of tasmaniasalmon
Should not have
• Not Shop at the end.

```html
<!DOCTYPE html>
<html lang="en">
<head>
<meta charset="utf-8">
<title>Reef Harvest – Business Card</title>
<link href="https://fonts.googleapis.com/css2?family=Montserrat:wght@400;700&display=swap" rel="stylesheet">
<style>
  :root {
    --backdrop: #c4c4c4;
    --card-white: #ffffff;
    --brand-teal: #1a9cc3;
    --ink: #2a2a2a;
    --photo-light: #f4f4f2;
    --photo-salmon: #e9875a;
    --photo-green: #6da23c;
    --photo-lemon: #f4d23a;
    --overlay-white: rgba(255, 255, 255, 0.72);
  }
  * { box-sizing: border-box; margin: 0; padding: 0; }
  html, body {
    width: 1200px;
    height: 800px;
    overflow: hidden;
    background: var(--backdrop);
    font-family: "Montserrat", sans-serif;
  }
  .card-set {
    position: absolute;
    inset: 0;
    display: flex;
    align-items: center;
    justify-content: center;
    gap: 50px;
  }
  .card {
    width: 530px;
    height: 303px;
    position: relative;
    overflow: hidden;
    background: var(--card-white);
    box-shadow: 0 4px 10px rgba(0, 0, 0, 0.25);
  }

  /* Front: logo and contact details */
  .card-front .brand {
    position: absolute;
    top: 58px;
    left: 150px;
    display: flex;
    align-items: center;
    gap: 12px;
  }
  .brand-dot {
    width: 22px;
    height: 22px;
    border-radius: 50%;
    background: var(--brand-teal);
  }
  .brand-name {
    font-weight: 700;
    font-size: 40px;
    letter-spacing: 0.5px;
    color: var(--brand-teal);
  }
  .contact-list {
    position: absolute;
    top: 150px;
    left: 64px;
    list-style: none;
    color: var(--ink);
    font-size: 17px;
    line-height: 1.35;
  }
  .contact-list li { display: flex; align-items: center; gap: 6px; }
  .contact-list .address { margin-bottom: 2px; }
  .contact-icon { width: 13px; height: 13px; flex: none; }

  /* Back: food photo with light overlay */
  .card-back .photo {
    position: absolute;
    inset: 0;
    background:
      radial-gradient(ellipse 38% 40% at 42% 48%, var(--photo-salmon) 0%, rgba(233,135,90,0.7) 55%, transparent 100%),
      radial-gradient(ellipse 18% 22% at 66% 72%, var(--photo-lemon) 0%, transparent 100%),
      radial-gradient(ellipse 30% 25% at 22% 30%, var(--photo-green) 0%, transparent 100%),
      radial-gradient(ellipse 20% 30% at 80% 40%, rgba(109,162,60,0.8) 0%, transparent 100%),
      linear-gradient(120deg, var(--photo-light) 0%, #eae6e0 50%, var(--photo-light) 100%);
  }
  .card-back .overlay-brand {
    position: absolute;
    top: 112px;
    left: 0;
    right: 0;
    text-align: center;
    font-weight: 700;
    font-size: 46px;
    color: var(--overlay-white);
  }
  .card-back .website {
    position: absolute;
    top: 178px;
    left: 0;
    right: 0;
    text-align: center;
    font-size: 16px;
    color: var(--ink);
  }
</style>
</head>
<body>
  <main class="card-set">
    <section class="card card-front" aria-label="Business card front">
      <div class="brand">
        <span class="brand-dot"></span>
        <span class="brand-name">Reef Harvest</span>
      </div>
      <ul class="contact-list">
        <li class="address">7/212-238 Kellaway Rd Marlin Point 4571</li>
        <li>
          <svg class="contact-icon" viewBox="0 0 14 14" aria-hidden="true">
            <rect width="14" height="14" rx="2" fill="#1a9cc3"/>
            <path d="M4 3.5c.6 0 1 1.6 1 2s-.8.6-.6 1.2 1.4 2 2 2.1 .8-.6 1.2-.6 2 .4 2 1-1 1.3-1.8 1.3C5.2 10.5 3 7.6 3 5c0-.8.4-1.5 1-1.5z" fill="#fff"/>
          </svg>
          0000-000-000
        </li>
        <li>
          <svg class="contact-icon" viewBox="0 0 14 14" aria-hidden="true">
            <rect width="14" height="14" rx="2" fill="#1a9cc3"/>
            <rect x="2.5" y="4" width="9" height="6.5" fill="#fff"/>
            <path d="M2.5 4l4.5 3.6L11.5 4" fill="none" stroke="#1a9cc3" stroke-width="1"/>
          </svg>
          email@
        </li>
      </ul>
    </section>

    <section class="card card-back" aria-label="Business card back">
      <div class="photo" role="img" aria-label="Photo of grilled salmon fillet with asparagus, snow peas, carrot and lemon wedges on a white plate"></div>
      <div class="overlay-brand">Reef Harvest</div>
      <div class="website">yourwebsite.com</div>
    </section>
  </main>
</body>
</html>
```